Create Website for new company called "Verdale Lodge 37"

Verdale Lodge 37 is a new business situated in Southwestern Colorado. We are creating a business that will rent out spaces where clients can grow their own marijuana. Picture a large green house with partitioned spaces that are secured by a lock. Best way to envision this would be to think of a storage business that rents out storage rooms. The difference is that we will be having the units inside a green house ( for growing purposes) Picture a small area that is secured by locks, Picture an area that has the ability to provide state of the art security, cameras etc. We want to focus our efforts on professionals, blue collar workers and end users of marijuana. Our emphasis is in the area of assisting those whom wish to grow their own plants. We want to provide them a safe facility in which to do that. . Keep in mind that we also build custom grow rooms at clients homes and provide a grow pod (lease these) where a small grow unit will be delivered and picked up from our clients whom want to lease a unit for a short amount of time. We have a business card ( just designed) and will send that information to those whom express an interests in this project. We want to be able to sign people up for our services by entering an agreement and signing the agreement while on the internet. We want to provide our services to those whom consume recreational and medical marijuana. This site will need to gather information I.e email addresses so that we can followup with offers. This is a tremendous opportunity for the right designer. We will be creating many more websites as other states come on line and make marijuana legal to consume. Use the business card model for a point of reference of how we envision the concept. That is a business card we just recently printed. The hands and the plant is our logo so far. Open to suggestions. There will be three levels of service. Bronze, Silver, Gold or Platinum. We will also have a retail biz down the road but not at the present time.

Target Market(s)

Ages 21-60

Industry/Entity Type

Medical

Logo Text

Verdale Lodge 37.

Number of Pages Required

5+ page

Requirements
Must have
• Clean appearance not to busy , easily navigable from link to link, page to page. Must have ability down the road to enter into a contractual agreement via the website. Must use our provided logo and example of that is on our business card that will be uploaded here shortly. We would like to have the colors that are on the business card however if you have suggestions or color schemes that you want us to consider that is okay.
Nice to have
• Nice to have a animation of seed to weed and how clients can save a tremendous amount of money growing their own cannabis. Nice to have testimonial page or feedback page. Have a membership component to website,
Should not have
• No flashing lights, etc. Not to busy in terms of animations.

```html
<!DOCTYPE html>
<html lang="en">
<head>
<meta charset="utf-8">
<title>Verdale Lodge 37</title>
<link href="https://fonts.googleapis.com/css2?family=Raleway:wght@400;500;700&family=Open+Sans:wght@400;600&display=swap" rel="stylesheet">
<style>
  :root {
    --orange: #c9702f;
    --orange-light: #dd8a45;
    --orange-dark: #a9561f;
    --green: #0f8a45;
    --green-dark: #0b6b35;
    --green-title: #157a3c;
    --footer-top: #1d5c3c;
    --footer-bottom: #0d3520;
    --text-dark: #333333;
    --text-body: #7a7a7a;
    --rule: #dcdcdc;
    --white: #ffffff;
  }
  * { box-sizing: border-box; margin: 0; padding: 0; }
  html, body { width: 965px; height: 1200px; overflow: hidden; background: var(--white); }
  body { position: relative; font-family: "Open Sans", sans-serif; color: var(--text-body); }
  .abs { position: absolute; }

  .hero {
    left: 0; top: 0; width: 965px; height: 520px;
    background: linear-gradient(180deg, #eef1f2 0%, #d7dcdc 22%, #c3cbc8 42%, #7fae5c 55%, #4f8f32 72%, #3c7a24 100%);
  }
  .brand {
    left: 0; top: 34px; width: 965px; text-align: center;
    font-family: "Raleway", sans-serif; font-weight: 700; font-size: 30px;
    color: #3a3a3a; letter-spacing: 0.5px;
  }
  .main-nav {
    left: 72px; top: 102px; width: 819px; height: 39px;
    background: linear-gradient(180deg, var(--orange-light), var(--orange-dark));
    border-bottom: 3px solid #4a2a14;
    display: flex; justify-content: center; align-items: center;
  }
  .main-nav a {
    font-family: "Raleway", sans-serif; font-weight: 500; font-size: 12px;
    color: var(--white); text-decoration: none; padding: 0 20px;
    border-left: 1px solid rgba(255,255,255,0.35); line-height: 16px;
  }
  .main-nav a:first-child { border-left: none; }

  .hero-panel {
    left: 75px; top: 264px; width: 347px; height: 123px;
    background: rgba(14,138,68,0.92); padding: 18px 0 0 23px; color: var(--white);
  }
  .hero-panel .lead { font-family: "Raleway", sans-serif; font-size: 19px; line-height: 22px; }
  .hero-panel .headline { font-family: "Raleway", sans-serif; font-weight: 500; font-size: 24px; line-height: 28px; }
  .hero-panel p { font-size: 8.5px; line-height: 16px; margin-top: 10px; color: #e4f3ea; }

  .slider-dots { left: 459px; top: 496px; display: flex; gap: 4px; }
  .slider-dots span { width: 11px; height: 11px; border-radius: 50%; background: var(--white); }

  h2 { font-family: "Raleway", sans-serif; font-weight: 400; }
  .welcome { left: 80px; top: 563px; width: 420px; }
  .welcome h2 { font-size: 22px; color: var(--text-dark); margin-bottom: 6px; }
  .welcome .intro { font-size: 11px; line-height: 16px; margin-bottom: 2px; }
  .welcome p { font-size: 9px; line-height: 16px; }
  .btn {
    display: inline-block; font-size: 9px; font-weight: 600; color: var(--white);
    text-transform: uppercase; text-align: center; width: 81px; height: 23px; line-height: 23px;
    border-radius: 2px;
  }
  .btn-orange { background: linear-gradient(180deg, #d07a38, var(--orange-dark)); }
  .btn-green { background: linear-gradient(180deg, #14934b, var(--green-dark)); }
  .welcome .btn { position: absolute; left: 1px; top: 123px; }

  .why { left: 548px; top: 563px; width: 340px; }
  .why h2 { font-size: 18px; color: var(--orange); }
  .why-photo {
    left: 551px; top: 597px; width: 128px; height: 109px;
    background: linear-gradient(160deg, #9cc46a, #4f8a2c 60%, #3a6e22);
  }
  .why-text { left: 693px; top: 594px; width: 200px; }
  .why-text h3 { font-size: 11px; font-weight: 400; color: var(--text-dark); margin-bottom: 3px; }
  .why-text p { font-size: 9px; line-height: 16px; }
  .why-btn { left: 693px; top: 686px; }

  .rule { left: 0; top: 759px; width: 965px; height: 1px; background: var(--rule); }

  .col { top: 800px; width: 262px; }
  .col h2 { font-size: 18px; color: var(--text-dark); margin-bottom: 12px; }
  .col .photo { width: 258px; height: 108px; margin-left: 2px; margin-bottom: 9px; }
  .col .sub { font-size: 11px; line-height: 16px; color: var(--text-body); margin-left: 2px; }
  .col p { font-size: 9px; line-height: 16px; margin-left: 2px; }
  .col p + p { margin-top: 4px; }
  .col-1 { left: 75px; }
  .col-2 { left: 363px; }
  .col-3 { left: 653px; }
  .col-3 h2 { color: var(--green-title); }
  .photo-bud { background: linear-gradient(90deg, #4c7a3a, #8cb56c 45%, #3f7a2e); }
  .photo-field { background: linear-gradient(180deg, #c7a274 0%, #b3966d 14%, #63a83a 22%, #4f9a2c 60%, #3a7c20 100%); }
  .post { margin-bottom: 10px; margin-left: 2px; }
  .post h3 { font-size: 11px; font-weight: 400; color: var(--text-dark); margin-bottom: 2px; }
  .post p { margin-left: 0; }

  .more-link {
    top: 1031px; font-size: 9.5px; font-weight: 600; color: var(--orange);
    text-transform: uppercase; display: flex; align-items: center; gap: 4px;
  }

  .site-footer {
    left: 0; top: 1106px; width: 965px; height: 94px;
    background: linear-gradient(180deg, var(--footer-top), var(--footer-bottom));
  }
  .footer-nav { left: 74px; top: 1129px; display: flex; font-size: 10.5px; color: var(--white); }
  .footer-nav a { color: var(--white); text-decoration: none; }
  .footer-nav .sep { padding: 0 6px; }
  .copyright { left: 74px; top: 1150px; font-size: 9px; color: #d6e4dc; }
  .social { left: 822px; top: 1130px; display: flex; gap: 10px; }
  .social span { width: 18px; height: 18px; border-radius: 50%; background: var(--white); }
</style>
</head>
<body>
  <div class="abs hero" role="img" aria-label="Photo of a large greenhouse interior with long rows of young green plants"></div>
  <div class="abs brand">Verdale Lodge 37</div>

  <nav class="abs main-nav">
    <a href="#">HOME</a><a href="#">ABOUT US</a><a href="#">SERVICES</a><a href="#">TESTIMONIALS</a><a href="#">BLOG</a><a href="#">OUR AREAS</a><a href="#">CONTACT US</a>
  </nav>

  <div class="abs hero-panel">
    <div class="lead">We Provide you Space for</div>
    <div class="headline">grow their own Marijuana</div>
    <p>Mauris vel lacus vitae felis vestibulum volutpat Etiam est nunc<br>venenatis in tristique eu imperdiet ac nisl Cum sociis</p>
  </div>
  <div class="abs slider-dots"><span></span><span></span><span></span><span></span></div>

  <section class="abs welcome">
    <h2>Welcome to Our Website Mainpage</h2>
    <div class="intro">Curabitur iaculis tempus eros Curabitur vel mi sit amet magna malesuada ultrices</div>
    <p>Etiam est nunc venenatis in tristique eu imperdiet ac nisl Cum sociis natoque penatibus et magnis dis parturient montes nascetur ridiculus mus In iaculis facilisis massa Etiam eu urna Sed porta Suspendisse quam leo molestie sed luctus quis feugiat in pede Fusce tellus Sed meFusce ultricies orci ac feugiat suscipit leo massa sodales velit et scelerisque mi tortor at ipsum</p>
    <a class="btn btn-orange" href="#">Read More</a>
  </section>

  <section class="abs why"><h2>Why Choose Us</h2></section>
  <div class="abs why-photo" role="img" aria-label="Photo of a grower in a straw hat tending tall cannabis plants"></div>
  <div class="abs why-text">
    <h3>Integer congue augue malesuada</h3>
    <p>nascetur ridiculus mus In iaculis facilisis massa Etiam eu urna Sed porta Suspendisse quam leo molestie sed luctus quis feugiat in pede Fusce tellus Sed me</p>
  </div>
  <a class="abs btn btn-green why-btn" href="#">Read More</a>

  <div class="abs rule"></div>

  <section class="abs col col-1">
    <h2>Marijuana Growth</h2>
    <div class="photo photo-bud" role="img" aria-label="Close-up photo of a flowering cannabis bud"></div>
    <div class="sub">Curabitur iaculis tempus eros Curabitur</div>
    <p>vel mi sit amet magna malesuada ultrices Ut nisi erat ferme ntum vel congue id euismod in elit Fusce ultricies orci ac feugiat suscipit leo massa sodales velit et sceleris</p>
  </section>

  <section class="abs col col-2">
    <h2>Services Provides</h2>
    <div class="photo photo-field" role="img" aria-label="Photo of green crop rows in an open field below brown hills"></div>
    <p>Lorem ipsum dolor sit amet consectetuer adipiscing elit Nam cursus Morbi ut mi Nullam enim leo egestas</p>
    <p>vel mi sit amet magna malesuada ultrices Ut nisi erat ferme ntum vel congue id euismod in elit Fusce ultricies orci ac</p>
  </section>

  <section class="abs col col-3">
    <h2>Recent Blog Post</h2>
    <div class="post"><h3>Integer congue augue malesuada</h3><p>nascetur ridiculus mus In iaculis facilisis massa Etiam eu urna Sed porta Suspendisse quam molestie</p></div>
    <div class="post"><h3>Morbi diam mauris viverra</h3><p>nascetur ridiculus mus In iaculis facilisis massa Etiam eu urna Sed porta Suspendisse quam molestie</p></div>
    <div class="post"><h3>Class aptent taciti sociosqu ad</h3><p>nascetur ridiculus mus In iaculis facilisis massa Etiam eu urna Sed porta Suspendisse quam molestie</p></div>
  </section>

  <a class="abs more-link" style="left:77px" href="#">Click here to read more
    <svg width="6" height="9" viewBox="0 0 6 9"><path d="M1 1l3.5 3.5L1 8" fill="none" stroke="#c9702f" stroke-width="1.8"/></svg></a>
  <a class="abs more-link" style="left:365px" href="#">View more services
    <svg width="6" height="9" viewBox="0 0 6 9"><path d="M1 1l3.5 3.5L1 8" fill="none" stroke="#c9702f" stroke-width="1.8"/></svg></a>
  <a class="abs more-link" style="left:655px" href="#">View more blog post
    <svg width="6" height="9" viewBox="0 0 6 9"><path d="M1 1l3.5 3.5L1 8" fill="none" stroke="#c9702f" stroke-width="1.8"/></svg></a>

  <footer class="abs site-footer"></footer>
  <nav class="abs footer-nav">
    <a href="#">HOME</a><span class="sep">|</span><a href="#">ABOUT US</a><span class="sep">|</span><a href="#">SERVICES</a><span class="sep">|</span><a href="#">TESTIMONIALS</a><span class="sep">|</span><a href="#">BLOG</a><span class="sep">|</span><a href="#">OUR AREAS</a><span class="sep">|</span><a href="#">CONTACT US</a>
  </nav>
  <div class="abs copyright">© 2014 Company Name &nbsp;All right reserved &nbsp;Term of Use</div>
  <div class="abs social">
    <span role="img" aria-label="Social link one"></span>
    <span role="img" aria-label="Social link two"></span>
    <span role="img" aria-label="Social link three"></span>
  </div>
</body>
</html>
```